Need a clean & modern homepage for an education site + opportunity for longer term work

Thanks for viewing our project. We are excited about this new website and we hope that we might build a relationship with designers as we work on this project. I provided quite a few details and requirements to help you more quickly create a design that meets our needs.
Who we are:
We are a website that discusses the importance of college accreditation and provides a directory of college programs.
What we need:
A homepage that meets the below requirements and is inspired by the examples provided
Definition of accredited:
ac·cred·it·ed [uh-kred-i-tid] adj.
1. officially recognized as meeting the essential requirements, as of academic excellence: accredited schools.
2. provided with official credentials, as by a government: an accredited diplomatic representative.
3. accepted as authoritative: an accredited theory.
Overall look and feel for the homepage:
- Clean, simple and modern
- Limited (or zero) pictures
- Utilize color blocks with text
- A trend seems to be longer vertical length homepages with lots of whitespace. I generally like this trend as long as the page is not way to tall.
Inspirations: Sites that have a similar look and feel to what I need.
http://lernvoxa.org/
http://www.campusmetrik.com/colleges/brantmoor-university/
http://quietfolding.org/
http://www.velostrahiring.com/
http://www.zunq.com/
http://sketches.bxv.com/
Items to be included on the homepage. Details below on each item.
- Top navigation
- Logo: Please leave a blank area for a logo. The logo has not been designed.
- Simple graphic/color block at the top that highlights a definition of “Accredited” – the definition should be formatted like it is being copy/pasted from a dictionary.
- Space for a video and small (50 word) written description of the video. You can use placeholder text.
- One section with 3 Paragraphs of content (each paragraph around 100 words) with a header at the top. You can use placeholder text but please create the formatting. At the end of the 3 paragraphs please have a “Read More” Note this shouldn't be 3 separate paragraphs with three read mores - it is 3 paragraphs with one read more at the end.
- An area with the header “Search Colleges by State” that has anchor text links to all 50 states.
Top navigation:
- Home
- States – with a subnav dropdown that includes all 50 US states.
- Programs – with a subnav dropdown that includes program titles (list below)
- Degrees - with a subnav dropdown that includes 5 degree levels (list below)
- Accreditation – no subnav
- Rankings – no subnav
- Resources – no subnav
Footer
- Link to about us, privacy, and a copyright www.url.com
Programs List for sub navigation
Accounting
Art
Bible
Business
Criminal Justice
Design
Education
Engineering
English
Law
LPN to RN
Management
Math
MBA
MPH
Medical Assisting
Military
Nursing
Occupational Therapy
Paralegal
Psychology
Pharmacy
RN to BSN
Radiology
Social Work
Sonography
Degrees list for sub navigation
Certificate
Associate
Bachelors
Masters
PhD
Thanks so much - looking forward to working with you!
Education

```html
<!DOCTYPE html>
<html lang="en">
<head>
<meta charset="utf-8">
<title>Accredited College Directory – Homepage</title>
<link href="https://fonts.googleapis.com/css2?family=Open+Sans:ital,wght@0,400;0,600;0,700;1,400;1,600&display=swap" rel="stylesheet">
<style>
  :root {
    --red: #e8585a;
    --blue: #3a9ad9;
    --green: #3bb08f;
    --ink: #333a40;
    --muted: #8a9096;
    --light: #b4b9be;
    --hero-top: #eef3f6;
    --hero-bottom: #b9c9d4;
    --band: #eef1f3;
    --footer: #f4f4f4;
    --rule: #dde1e4;
    --white: #ffffff;
  }
  * { box-sizing: border-box; margin: 0; padding: 0; }
  html, body { width: 720px; height: 1200px; overflow: hidden; background: var(--white); }
  body { font-family: "Open Sans", Arial, sans-serif; color: var(--ink); position: relative; }

  /* header */
  .site-header { position: absolute; left: 0; top: 0; width: 720px; height: 60px; background: var(--white); border-bottom: 1px solid var(--rule); }
  .logo { position: absolute; left: 24px; top: 18px; font-size: 15px; font-weight: 700; letter-spacing: 0.5px; color: var(--ink); border-bottom: 2px solid var(--ink); padding-bottom: 2px; }
  .main-nav { position: absolute; right: 24px; top: 22px; font-size: 10px; color: var(--muted); }
  .main-nav span { padding: 0 4px; }
  .main-nav .sep { color: var(--light); padding: 0; }

  /* hero */
  .hero { position: absolute; left: 0; top: 60px; width: 720px; height: 290px; background: linear-gradient(180deg, var(--hero-top) 0%, #dfe8ee 45%, var(--hero-bottom) 100%); overflow: hidden; }
  .hero-art { position: absolute; left: 0; bottom: 0; width: 720px; height: 160px; background: linear-gradient(180deg, rgba(160,182,198,0) 0%, rgba(140,164,182,0.55) 55%, #8fa6b6 100%); }
  .hero-title { position: absolute; left: 90px; top: 18px; font-size: 17px; line-height: 22px; font-weight: 400; color: var(--ink); }
  .hero-title strong { font-weight: 700; }
  .definition { position: absolute; left: 90px; top: 66px; width: 460px; font-size: 9.5px; line-height: 13px; color: var(--muted); }
  .definition .term { font-weight: 700; color: var(--ink); }
  .definition .pron { font-style: italic; }
  .search-bar { position: absolute; left: 90px; top: 100px; height: 30px; }
  .search-input { position: absolute; left: 0; top: 0; width: 270px; height: 30px; background: var(--white); border: 1px solid var(--rule); font-size: 10px; color: var(--muted); padding: 8px 10px; }
  .search-state { position: absolute; left: 280px; top: 0; width: 100px; height: 30px; background: var(--white); border: 1px solid var(--rule); font-size: 10px; color: var(--muted); padding: 8px 10px; }
  .search-state svg { position: absolute; right: 9px; top: 12px; }
  .search-btn { position: absolute; left: 388px; top: 0; width: 64px; height: 30px; background: var(--red); color: var(--white); font-size: 10px; font-weight: 600; text-align: center; line-height: 30px; }

  /* intro + video */
  .intro-text { position: absolute; left: 40px; top: 378px; width: 320px; font-size: 9.5px; line-height: 14px; color: var(--muted); }
  .video-frame { position: absolute; left: 400px; top: 370px; width: 240px; height: 120px; background: linear-gradient(135deg, #dfe7ec 0%, #b9cad6 100%); }
  .video-frame svg { position: absolute; left: 100px; top: 40px; }
  .btn { position: absolute; background: var(--red); color: var(--white); font-size: 10.5px; font-weight: 600; text-align: center; }
  .watch-btn { left: 445px; top: 500px; width: 150px; height: 28px; line-height: 28px; }

  /* feature cards */
  .features { position: absolute; left: 0; top: 545px; width: 720px; height: 245px; background: var(--band); }
  .feature { position: absolute; top: 0; width: 200px; text-align: center; }
  .feature-icon { position: absolute; left: 60px; top: 20px; width: 80px; height: 80px; border-radius: 50%; }
  .feature-icon svg { position: absolute; left: 20px; top: 20px; }
  .feature-title { position: absolute; left: 0; top: 112px; width: 200px; font-size: 18px; font-weight: 600; color: var(--ink); }
  .feature-text { position: absolute; left: 10px; top: 142px; width: 180px; font-size: 8.5px; line-height: 12px; color: var(--muted); }
  .feature .btn { left: 45px; top: 210px; width: 110px; height: 24px; line-height: 24px; }

  /* content section */
  .section-title { position: absolute; left: 30px; top: 830px; width: 220px; font-size: 26px; line-height: 31px; font-style: italic; color: var(--red); }
  .section-rule { position: absolute; left: 270px; top: 808px; width: 420px; height: 2px; background: var(--red); }
  .article { position: absolute; left: 270px; width: 420px; }
  .article h3 { font-size: 13px; font-weight: 400; font-style: italic; color: var(--ink); margin-bottom: 3px; }
  .article p { font-size: 8.5px; line-height: 12px; color: var(--muted); }
  .more-btn { left: 580px; top: 1010px; width: 110px; height: 24px; line-height: 24px; }

  /* footer */
  .site-footer { position: absolute; left: 0; top: 1048px; width: 720px; height: 127px; border-top: 1px solid var(--rule); }
  .social { position: absolute; left: 540px; top: 4px; height: 8px; line-height: 0; }
  .social i { display: inline-block; width: 8px; height: 8px; border-radius: 50%; background: var(--light); margin-right: 8px; }
  .footer-head { position: absolute; top: 20px; font-size: 13px; line-height: 16px; font-weight: 700; color: var(--ink); }
  .footer-head .dot { display: inline-block; width: 9px; height: 9px; border-radius: 50%; background: var(--ink); margin-right: 5px; }
  .link-list { position: absolute; top: 39px; list-style: none; font-size: 8px; line-height: 9px; color: var(--muted); }
  .bottom-bar { position: absolute; left: 0; top: 1175px; width: 720px; height: 25px; background: var(--footer); border-top: 1px solid var(--rule); font-size: 9.5px; color: var(--muted); }
  .copyright { position: absolute; left: 30px; top: 6px; }
  .legal-links { position: absolute; right: 30px; top: 6px; }
  .legal-links span { margin-left: 14px; }
</style>
</head>
<body>

<header class="site-header">
  <div class="logo">MY WEBSITE NAME</div>
  <nav class="main-nav">
    <span>Home</span><span class="sep">|</span><span>States</span><span class="sep">|</span><span>Programs</span><span class="sep">|</span><span>Degrees</span><span class="sep">|</span><span>Accreditation</span><span class="sep">|</span><span>Rankings</span><span class="sep">|</span><span>Resources</span>
  </nav>
</header>

<section class="hero">
  <div class="hero-art" role="img" aria-label="Soft blue-grey illustration of a town of houses with a ladder leading upward"></div>
  <h1 class="hero-title"><strong>Simple graphic/color block at the top that</strong><br>highlights a definition of "Accredited"</h1>
  <p class="definition"><span class="term">ac·cred·it·ed</span> <span class="pron">[uh-kred-i-tid] adj.</span> 1. officially recognized as meeting the essential requirements, as of academic excellence: accredited schools.</p>
  <div class="search-bar">
    <div class="search-input">Search College</div>
    <div class="search-state">State
      <svg width="8" height="5" viewBox="0 0 8 5"><path d="M0 0 L4 5 L8 0 Z" fill="#8a9096"/></svg>
    </div>
    <div class="search-btn">SEARCH</div>
  </div>
</section>

<p class="intro-text">A short written description of the video goes here, explaining what viewers will learn about college accreditation, why it matters when choosing a school, and how to use our directory to compare accredited programs by state, degree level and field of study before applying anywhere. Watch the full clip to see real examples of accrediting agencies and the questions every student should ask.</p>

<div class="video-frame" role="img" aria-label="Video still of a presenter introducing college accreditation">
  <svg width="40" height="40" viewBox="0 0 40 40"><circle cx="20" cy="20" r="19" fill="#ffffff" opacity="0.85"/><path d="M16 12 L28 20 L16 28 Z" fill="#3a9ad9"/></svg>
</div>
<div class="btn watch-btn">Watch video</div>

<section class="features">
  <div class="feature" style="left:20px;">
    <div class="feature-icon" style="background:var(--blue);">
      <svg width="40" height="40" viewBox="0 0 40 40"><path d="M2 15 L20 7 L38 15 L20 23 Z" fill="#fff"/><path d="M10 19 V28 C14 32 26 32 30 28 V19 L20 24 Z" fill="#fff"/><path d="M35 16 V26" stroke="#fff" stroke-width="2"/></svg>
    </div>
    <div class="feature-title">Ranking</div>
    <p class="feature-text">One section with 3 Paragraphs of content (each paragraph around 100 words) with a header at the top. You can use placeholder text but please create the formatting.</p>
    <div class="btn">Read more</div>
  </div>
  <div class="feature" style="left:260px;">
    <div class="feature-icon" style="background:var(--green);">
      <svg width="40" height="40" viewBox="0 0 40 40"><circle cx="20" cy="16" r="13" fill="#fff"/><path d="M12 26 L8 38 L14 35 L17 39 L20 29 Z M28 26 L32 38 L26 35 L23 39 L20 29 Z" fill="#fff"/><path d="M14 16 L18 20 L26 11" stroke="#3bb08f" stroke-width="3" fill="none"/></svg>
    </div>
    <div class="feature-title">Accreditation</div>
    <p class="feature-text">One section with 3 Paragraphs of content (each paragraph around 100 words) with a header at the top. You can use placeholder text but please create the formatting.</p>
    <div class="btn">Read more</div>
  </div>
  <div class="feature" style="left:500px;">
    <div class="feature-icon" style="background:var(--blue);">
      <svg width="40" height="40" viewBox="0 0 40 40"><rect x="8" y="4" width="24" height="32" rx="2" fill="#fff"/><path d="M13 12 H27 M13 18 H27 M13 24 H23" stroke="#3a9ad9" stroke-width="2.5"/></svg>
    </div>
    <div class="feature-title">Resources</div>
    <p class="feature-text">One section with 3 Paragraphs of content (each paragraph around 100 words) with a header at the top. You can use placeholder text but please create the formatting.</p>
    <div class="btn">Read more</div>
  </div>
</section>

<h2 class="section-title">Your section title here explain small-desc</h2>
<div class="section-rule"></div>
<article class="article" style="top:818px;">
  <h3>header at the top</h3>
  <p>One section with 3 Paragraphs of content (each paragraph around 100 words) with a header at the top. You can use placeholder text but please create the formatting. At the end of the 3 paragraphs please have a "Read More". Note this shouldn't be 3 separate paragraphs with three read mores – it is 3 paragraphs with one read more at the end.</p>
</article>
<article class="article" style="top:884px;">
  <h3>header at the top</h3>
  <p>One section with 3 Paragraphs of content (each paragraph around 100 words) with a header at the top. You can use placeholder text but please create the formatting. At the end of the 3 paragraphs please have a "Read More". Note this shouldn't be 3 separate paragraphs with three read mores – it is 3 paragraphs with one read more at the end.</p>
</article>
<article class="article" style="top:950px;">
  <h3>header at the top</h3>
  <p>One section with 3 Paragraphs of content (each paragraph around 100 words) with a header at the top. You can use placeholder text but please create the formatting. At the end of the 3 paragraphs please have a "Read More". Note this shouldn't be 3 separate paragraphs with three read mores – it is 3 paragraphs with one read more at the end.</p>
</article>
<div class="btn more-btn">Read more</div>

<footer class="site-footer">
  <div class="social"><i></i><i></i><i></i><i></i><i></i><i></i></div>
  <div class="footer-head" style="left:30px;">Programs</div>
  <ul class="link-list" style="left:30px;"><li>Accounting</li><li>Art</li><li>Bible</li><li>Business</li><li>Criminal Justice</li><li>Design</li><li>Education</li><li>Engineering</li><li>English</li></ul>
  <ul class="link-list" style="left:180px;"><li>Law</li><li>LPN to RN</li><li>Management</li><li>Math</li><li>MBA</li><li>MPH</li><li>Medical Assisting</li><li>Military</li><li>Nursing</li></ul>
  <div class="footer-head" style="left:370px;">Degrees</div>
  <ul class="link-list" style="left:370px;"><li>Certificate</li><li>Associate</li><li>Bachelors</li><li>Masters</li><li>PhD</li></ul>
  <div class="footer-head" style="left:510px;"><span class="dot"></span>Colleges by State</div>
  <ul class="link-list" style="left:524px;"><li>Alabama</li><li>Alaska</li><li>Arizona</li><li>Arkansas</li><li>California</li><li>Colorado</li><li>Connecticut</li><li>Delaware</li><li>Florida</li></ul>
  <ul class="link-list" style="left:614px;"><li>Georgia</li><li>Hawaii</li><li>Idaho</li><li>Illinois</li><li>Indiana</li><li>Iowa</li><li>Kansas</li><li>Kentucky</li><li>Louisiana</li></ul>
</footer>

<div class="bottom-bar">
  <span class="copyright">copyright@www.url.com</span>
  <span class="legal-links"><span>about us</span><span>privacy</span></span>
</div>

</body>
</html>
```